Icons/images for company values

We have five company values, we have a new logo and a new look. I would like drawn images for each value that are in keeping with our look and feel.

Target Market(s)

internal/staff

Industry/Entity Type

media compliance

Requirements
Must have
• colours aligned with logo.

```html
<!DOCTYPE html>
<html lang="en">
<head>
<meta charset="utf-8">
<title>Kovala Values 2023</title>
<link href="https://fonts.googleapis.com/css2?family=Lexend:wght@800&family=Poppins:wght@400;500&family=Outfit:wght@500;600&display=swap" rel="stylesheet">
<style>
  :root {
    --page: #ffffff;
    --navy: #040b26;
    --core: #0c2142;
    --teal: #2fb8a8;
    --green: #8ff08a;
    --lime: #d4ea4c;
    --blue: #1a8fd0;
    --white: #ffffff;
  }
  html, body { margin: 0; width: 1200px; height: 1200px; overflow: hidden; background: var(--page); }
  .stage { position: relative; width: 1200px; height: 1200px; }
  .poster {
    position: absolute; left: 0; top: 176px;
    width: 1535px; height: 1085px;
    transform: scale(0.7818); transform-origin: 0 0;
    overflow: hidden;
    background: radial-gradient(ellipse 70% 40% at 85% 40%, #0b2160 0%, rgba(11,33,96,0) 70%),
                radial-gradient(ellipse 60% 50% at 30% 70%, #0a1a4a 0%, rgba(10,26,74,0) 70%),
                var(--navy);
  }
  .brand-name {
    position: absolute; left: 100px; top: 150px; margin: 0;
    font-family: "Poppins", sans-serif; font-weight: 500; font-size: 44px;
    letter-spacing: 0; color: var(--white);
  }
  .graphic { position: absolute; left: 0; top: 0; }
  .value-card {
    position: absolute; box-sizing: border-box;
    border: 1.5px dashed var(--teal); border-radius: 18px;
  }
  .value-card::before {
    content: ""; position: absolute; left: -1px; top: -1px;
    width: 62px; height: 62px; border-top-left-radius: 18px;
    background: linear-gradient(135deg, var(--teal) 50%, transparent 50%);
  }
  .value-card .dot {
    position: absolute; bottom: -6px; width: 10px; height: 10px; border-radius: 50%;
    background: var(--teal);
  }
  .value-title {
    margin: 0; font-family: "Lexend", sans-serif; font-weight: 800;
    text-transform: uppercase; letter-spacing: 0;
  }
  .value-text {
    margin: 6px 0 0; font-family: "Poppins", sans-serif; font-weight: 400;
    font-size: 15px; line-height: 20px; color: var(--white);
  }
  .card-leaders { left: 582px; top: 122px; width: 373px; height: 248px; padding: 24px 0 0 41px; border-color: #c9e36a; }
  .card-leaders .value-title { color: var(--green); font-size: 24px; line-height: 30px; }
  .card-leaders .value-text { width: 305px; margin-top: 2px; }
  .card-faster { left: 212px; top: 403px; width: 368px; height: 222px; padding: 50px 0 0 30px; }
  .card-faster .value-title { color: var(--lime); font-size: 26px; line-height: 31px; }
  .card-faster .value-text { width: 275px; margin-top: 10px; }
  .card-done { left: 962px; top: 400px; width: 371px; height: 225px; padding: 36px 0 0 54px; border-color: #b8e36a; }
  .card-done .value-title { color: var(--green); font-size: 22px; line-height: 24px; }
  .card-done .value-text { width: 290px; margin-top: 18px; }
  .card-open { left: 65px; top: 702px; width: 368px; height: 223px; padding: 24px 0 0 37px; }
  .card-open .value-title { color: var(--lime); font-size: 26px; line-height: 31px; }
  .card-open .value-text { width: 290px; margin-top: 6px; }
  .card-diverse { left: 1089px; top: 700px; width: 371px; height: 226px; padding: 26px 0 0 62px; border-color: #c9e36a; }
  .card-diverse .value-title { color: var(--blue); font-size: 22px; line-height: 24px; }
  .card-diverse .value-text { width: 255px; margin-top: 14px; }
  .values-label {
    position: absolute; left: 572px; width: 400px; top: 868px; margin: 0;
    text-align: center; color: var(--white); font-family: "Outfit", sans-serif;
  }
  .values-label .word { display: block; font-size: 68px; font-weight: 500; line-height: 66px; }
  .values-label .year { display: block; font-size: 96px; font-weight: 600; line-height: 88px; }
</style>
</head>
<body>
<main class="stage">
  <section class="poster">
    <h1 class="brand-name">Kovala</h1>

    <svg class="graphic" width="1535" height="1085" viewBox="0 0 1535 1085" aria-hidden="true">
      <defs>
        <linearGradient id="ring-fill" x1="0" y1="1" x2="1" y2="0">
          <stop offset="0" stop-color="#1e8fc4"/>
          <stop offset="0.35" stop-color="#6fe3a0"/>
          <stop offset="0.65" stop-color="#a9f07e"/>
          <stop offset="1" stop-color="#e0ea5a"/>
        </linearGradient>
      </defs>
      <g stroke="#c9e36a" stroke-width="1.5" stroke-dasharray="5 4" fill="none">
        <line x1="768" y1="370" x2="768" y2="620"/>
        <line x1="580" y1="405" x2="580" y2="682"/>
        <line x1="962" y1="600" x2="962" y2="682"/>
      </g>
      <circle cx="772" cy="1012" r="332" fill="url(#ring-fill)"/>
      <g stroke="#3c8f7e" stroke-width="2" opacity="0.6">
        <line x1="772" y1="1012" x2="668" y2="695"/>
        <line x1="772" y1="1012" x2="875" y2="695"/>
        <line x1="772" y1="1012" x2="505" y2="818"/>
        <line x1="772" y1="1012" x2="1040" y2="818"/>
      </g>
      <circle cx="772" cy="1012" r="245" fill="#081632"/>
      <circle cx="772" cy="1012" r="222" fill="var(--core)"/>

      <g class="icon-badges">
        <circle cx="458" cy="912" r="60" fill="#4fd6a8"/>
        <circle cx="572" cy="740" r="60" fill="#8cef95"/>
        <circle cx="768" cy="677" r="60" fill="#b6f07a"/>
        <circle cx="963" cy="740" r="60" fill="#cfee66"/>
        <circle cx="1080" cy="912" r="60" fill="#d7ec5c"/>
        <g fill="var(--navy)">
          <circle cx="458" cy="912" r="50"/><circle cx="572" cy="740" r="50"/>
          <circle cx="768" cy="677" r="50"/><circle cx="963" cy="740" r="50"/>
          <circle cx="1080" cy="912" r="50"/>
        </g>
        <g fill="none" stroke="#ffffff" stroke-width="2.2" stroke-linecap="round" stroke-linejoin="round">
          <path d="M458 902 c-6-10 -22-6 -16 6 l16 14 16-14 c6-12 -10-16 -16-6z"/>
          <path d="M430 905 v20 l14 14 v8 M486 905 v20 l-14 14 v8 M438 918 l10 10 M478 918 l-10 10"/>
          <rect x="542" y="745" width="60" height="16" rx="2"/>
          <path d="M550 742 a22 22 0 0 1 44 0 M572 742 l6 -12 M561 752 h25"/>
          <circle cx="768" cy="680" r="8"/><circle cx="750" cy="672" r="6"/><circle cx="786" cy="672" r="6"/>
          <path d="M752 704 a16 16 0 0 1 32 0 M738 692 a12 12 0 0 1 18 -8 M798 692 a12 12 0 0 0 -18 -8"/>
          <path d="M768 694 l4 8 9 1 -7 6 2 9 -8 -5 -8 5 2 -9 -7 -6 9 -1z"/>
          <circle cx="958" cy="735" r="20"/>
          <path d="M949 735 l7 7 12 -13 M968 748 v14 h10 v-10 l-6 -2"/>
          <circle cx="1080" cy="903" r="16"/>
          <path d="M1073 903 l5 5 9 -10 M1070 918 l-8 16 8 -2 4 7 8 -14 M1090 918 l8 16 -8 -2 -4 7 -8 -14"/>
        </g>
      </g>
    </svg>

    <article class="value-card card-leaders">
      <h2 class="value-title">We are leaders in copyright and intellectual property</h2>
      <p class="value-text">Leading the conversation in audio-visual copyright compliance and advocating for the protection of intellectual property globally.</p>
      <span class="dot" style="left:339px;background:#c9e36a"></span>
    </article>

    <article class="value-card card-faster">
      <h2 class="value-title">We get&nbsp; there<br>faster together</h2>
      <p class="value-text">Collaboration is at the heart of what we do, no matter our team</p>
      <span class="dot" style="left:271px;background:#8ff08a"></span>
    </article>

    <article class="value-card card-done">
      <h2 class="value-title">We get things<br>done</h2>
      <p class="value-text">We grow through capability, focus and hard work. We believe small steps compound to bigresults.</p>
      <span class="dot" style="left:89px"></span>
    </article>

    <article class="value-card card-open">
      <h2 class="value-title">We're open<br>and honest</h2>
      <p class="value-text">Sharing information helps us achieve the best outcomes for our teams and business. We value open, honest, and clear communication.</p>
      <span class="dot" style="left:270px"></span>
    </article>

    <article class="value-card card-diverse">
      <h2 class="value-title">Diverse<br>perspectives build<br>better outcomes</h2>
      <p class="value-text">We value diversity, inclusion, respect and trust within our teams. We are building a truly global organisation.</p>
      <span class="dot" style="left:89px"></span>
    </article>

    <h2 class="values-label"><span class="word">VALUES</span><span class="year">2023</span></h2>
  </section>
</main>
</body>
</html>
```